Design bcard for Valtrove Consulting and Training LLC

I need a logo inspired by the term Valtrove. I'd like to have type of work I do on the back side, i.e. provide V and T on DEIJ, SDOH,...... Front of card--business name, contact information, and possibly a tag line.

Target Market(s)

NGOs, human service agencies, education, healthcare, public health.

Contact Information for Business Card

Name of business, email address, phone number, logo--on front. Services on the back

Font styles to use
Sans Serif

Requirements
Must have
• Contact information, creative logo, services

```html
<!DOCTYPE html>
<html lang="en">
<head>
<meta charset="utf-8">
<title>Valtrove Consulting and Training LLC – Business Cards</title>
<link rel="stylesheet" href="https://fonts.googleapis.com/css2?family=Lato:wght@400;700&display=swap">
<style>
  :root {
    --blue: #1a7dbe;
    --purple: #a04a9b;
    --ink: #3a3a3a;
    --paper: #ffffff;
    --edge: #e4e4e4;
  }
  * { margin: 0; padding: 0; box-sizing: border-box; }
  html, body { width: 1200px; height: 818px; overflow: hidden; background: var(--paper); }
  body { position: relative; font-family: "Lato", sans-serif; }

  .card {
    position: absolute;
    width: 449px; height: 257px;
    background: var(--paper);
    border: 1px solid var(--edge);
    border-radius: 14px;
    box-shadow: 0 2px 3px rgba(0,0,0,0.28);
    overflow: hidden;
  }
  .card--front-a { left: 127px; top: 129px; }
  .card--front-b { left: 626px; top: 129px; }
  .card--back-a  { left: 127px; top: 433px; }
  .card--back-b  { left: 626px; top: 433px; }

  .front__waves { position: absolute; inset: 0; }

  .person { position: absolute; left: 40px; top: 24px; }
  .person__name {
    color: var(--blue); font-weight: 700; font-size: 21px;
    letter-spacing: 1px; line-height: 1;
  }
  .person__role {
    color: var(--purple); font-size: 13px; letter-spacing: 0.6px;
    margin-top: 6px;
  }
  .person__rule { width: 25px; height: 2px; background: var(--blue); margin-top: 9px; }

  .contact { position: absolute; left: 40px; top: 89px; list-style: none; }
  .contact__item {
    display: flex; align-items: center; gap: 9px;
    height: 17px; font-size: 11px; color: var(--ink); letter-spacing: 1px;
  }
  .contact__icon { width: 9px; height: 9px; fill: var(--purple); flex: none; }

  .front__mark {
    position: absolute; left: 354px; top: 66px;
    width: 54px; height: 54px; border-radius: 50%;
    background: var(--purple);
  }

  .tagline {
    position: absolute; left: 0; right: 0; top: 238px;
    text-align: center; color: #fff; font-size: 11px; letter-spacing: 0.6px;
  }

  .brand {
    position: absolute; left: 0; right: 0; top: 58px;
    display: flex; flex-direction: column; align-items: center;
    color: var(--blue); font-weight: 700;
  }
  .brand__row { display: flex; align-items: center; gap: 10px; }
  .brand__dot { width: 16px; height: 16px; border-radius: 50%; background: var(--purple); }
  .brand__name { font-size: 52px; line-height: 1; letter-spacing: 0.5px; }
  .brand__legal { font-size: 13px; letter-spacing: 3.6px; margin-top: 8px; }

  .services {
    position: absolute; left: 0; right: 0; top: 206px;
    text-align: center; color: var(--ink); font-size: 11px; line-height: 15px;
  }
</style>
</head>
<body>

  <!-- Front, variant A -->
  <section class="card card--front-a">
    <svg class="front__waves" viewBox="0 0 449 257" width="449" height="257" aria-hidden="true">
      <path d="M0 181 Q220 262 402 202 Q220 258 0 193 Z" fill="var(--purple)"/>
      <path d="M0 198 Q230 270 449 192 L449 257 L0 257 Z" fill="var(--blue)"/>
    </svg>
    <div class="front__mark" aria-hidden="true"></div>
    <div class="person">
      <div class="person__name">MAREN ELLERY</div>
      <div class="person__role">Founder &amp; CEO</div>
      <div class="person__rule"></div>
    </div>
    <ul class="contact">
      <li class="contact__item"><svg class="contact__icon" viewBox="0 0 10 10"><path d="M2 0.5 L3.6 2.6 L2.7 3.6 Q4 6 6.4 7.3 L7.4 6.4 L9.5 8 L8.3 9.5 Q3 8.5 0.5 1.7 Z"/></svg>(555) 214-3807</li>
      <li class="contact__item"><svg class="contact__icon" viewBox="0 0 10 10"><path d="M2.5 0 H7.5 V10 H2.5 Z M3.5 1 V8 H6.5 V1 Z"/></svg>(555) 318-6092</li>
      <li class="contact__item"><svg class="contact__icon" viewBox="0 0 10 10"><path d="M2.5 0 H7.5 V3 H2.5 Z M0.5 3.5 H9.5 V7.5 H8 V6 H2 V7.5 H0.5 Z M2.5 6.5 H7.5 V10 H2.5 Z"/></svg>(555) 427-1536</li>
      <li class="contact__item"><svg class="contact__icon" viewBox="0 0 10 10"><path d="M0.5 2 H9.5 V8.5 H0.5 Z M1.2 2.6 L5 5.6 L8.8 2.6 Z" fill-rule="evenodd"/></svg>hello@valtrovect.com</li>
      <li class="contact__item"><svg class="contact__icon" viewBox="0 0 10 10"><path d="M5 0.5 A4.5 4.5 0 1 1 4.99 0.5 Z M5 1.6 A3.4 3.4 0 1 0 5.01 1.6 Z M3 3 L5 2.5 L6 4.5 L4 6 Z" fill-rule="evenodd"/></svg>valtrovect.com</li>
    </ul>
    <div class="tagline">YOUR TAGLINE GOES HERE</div>
  </section>

  <!-- Front, variant B -->
  <section class="card card--front-b">
    <svg class="front__waves" viewBox="0 0 449 257" width="449" height="257" aria-hidden="true">
      <path d="M0 181 Q220 262 402 202 Q220 258 0 193 Z" fill="var(--purple)"/>
      <path d="M0 198 Q230 270 449 192 L449 257 L0 257 Z" fill="var(--blue)"/>
    </svg>
    <div class="front__mark" aria-hidden="true"></div>
    <div class="person">
      <div class="person__name">MAREN ELLERY</div>
      <div class="person__role">Founder &amp; CEO</div>
      <div class="person__rule"></div>
    </div>
    <ul class="contact">
      <li class="contact__item"><svg class="contact__icon" viewBox="0 0 10 10"><path d="M2 0.5 L3.6 2.6 L2.7 3.6 Q4 6 6.4 7.3 L7.4 6.4 L9.5 8 L8.3 9.5 Q3 8.5 0.5 1.7 Z"/></svg>(555) 214-3807</li>
      <li class="contact__item"><svg class="contact__icon" viewBox="0 0 10 10"><path d="M2.5 0 H7.5 V10 H2.5 Z M3.5 1 V8 H6.5 V1 Z"/></svg>(555) 318-6092</li>
      <li class="contact__item"><svg class="contact__icon" viewBox="0 0 10 10"><path d="M2.5 0 H7.5 V3 H2.5 Z M0.5 3.5 H9.5 V7.5 H8 V6 H2 V7.5 H0.5 Z M2.5 6.5 H7.5 V10 H2.5 Z"/></svg>(555) 427-1536</li>
      <li class="contact__item"><svg class="contact__icon" viewBox="0 0 10 10"><path d="M0.5 2 H9.5 V8.5 H0.5 Z M1.2 2.6 L5 5.6 L8.8 2.6 Z" fill-rule="evenodd"/></svg>hello@valtrovect.com</li>
      <li class="contact__item"><svg class="contact__icon" viewBox="0 0 10 10"><path d="M5 0.5 A4.5 4.5 0 1 1 4.99 0.5 Z M5 1.6 A3.4 3.4 0 1 0 5.01 1.6 Z M3 3 L5 2.5 L6 4.5 L4 6 Z" fill-rule="evenodd"/></svg>valtrovect.com</li>
    </ul>
    <div class="tagline">YOUR TAGLINE GOES HERE</div>
  </section>

  <!-- Back, variant A -->
  <section class="card card--back-a">
    <div class="brand">
      <div class="brand__row">
        <span class="brand__dot" aria-hidden="true"></span>
        <span class="brand__name">VALTROVE</span>
      </div>
      <span class="brand__legal">CONSULTING AND TRAINING LLC</span>
    </div>
    <p class="services">Health Care &amp; Quality | Neihgborhood &amp; Built Environment | Ecnomic Stability<br>Social and Community Context | Education Access and Quality</p>
  </section>

  <!-- Back, variant B -->
  <section class="card card--back-b">
    <div class="brand">
      <div class="brand__row">
        <span class="brand__dot" aria-hidden="true"></span>
        <span class="brand__name">VALTROVE</span>
      </div>
      <span class="brand__legal">CONSULTING AND TRAINING LLC</span>
    </div>
    <p class="services">Health Care &amp; Quality | Neihgborhood &amp; Built Environment | Ecnomic Stability<br>Social and Community Context | Education Access and Quality</p>
  </section>

</body>
</html>
```